Bram Keystone Homes needs a business card

We need a business card for a new company in Canada, Ontario. Our company is all about luxury contraction homes for our clients. Our product and services are custom projects design. Under the business logo that will be created, we want a slogan that will be a memorable phrase for consumers to remember us to tell their friends and relatives.

Additional infomation
- Ludovic Entrasse
- President / Ceo
-519.604.3087

Find point what luxury construction products and services can be done

We like to see colors:
- #663300
- and something other colors or color that would attract the client needs and wants

The final design should communicate leads from new or old clients that will grow our empire. Most of all, we try to work among the budget that clients want

NOTE
- we also need an icon for the business (Example: Instagram, Facebook, and Whatsapp icons)
- We want the company name to be remembered easily for clients and our distributors who would get our orders.
- we need an icon on the business cards: Facebook and Instagram.

Thanks,
Bram Keystone Homes

```html
<!DOCTYPE html>
<html lang="en">
<head>
<meta charset="utf-8">
<title>Bram Keystone Homes — Business Card</title>
<link rel="stylesheet" href="https://fonts.googleapis.com/css2?family=Arimo:wght@400;700&display=swap">
<style>
  :root {
    --page-bg: #2b2b2f;
    --card-bg: #1d2022;
    --silver: #b4b7ba;
    --brand-brown: #7a3f14;
    --band-brown: #663300;
  }
  * { box-sizing: border-box; margin: 0; padding: 0; }
  html, body {
    width: 1200px; height: 800px; overflow: hidden;
    background: var(--page-bg);
    font-family: "Arimo", Arial, sans-serif;
  }
  .canvas {
    width: 1200px; height: 800px;
    display: flex; flex-direction: column; align-items: center; justify-content: center;
    gap: 44px;
  }
  .card {
    position: relative;
    width: 600px; height: 343px;
    background: var(--card-bg);
    box-shadow: 0 10px 30px rgba(0,0,0,.45);
    overflow: hidden;
  }
  .wordmark {
    font-family: "Arimo", Arial, sans-serif;
    font-weight: 700;
    font-size: 40px;
    line-height: 1;
    white-space: nowrap;
  }
  .slogan {
    font-size: 13px;
    letter-spacing: .3px;
    white-space: nowrap;
    margin-top: 10px;
  }

  /* Front */
  .card--front .brand {
    position: absolute; left: 50%; top: 50%;
    transform: translate(-50%, -50%);
    text-align: center;
  }
  .card--front .wordmark,
  .card--front .slogan { color: var(--silver); }

  /* Back */
  .card--back .brand {
    position: absolute; left: 36px; top: 92px;
  }
  .card--back .wordmark { color: var(--brand-brown); font-size: 36px; }
  .card--back .slogan { color: var(--brand-brown); font-size: 12px; }

  .divider {
    position: absolute; left: 408px; top: 150px;
    width: 1px; height: 120px;
    background: var(--brand-brown);
  }
  .contact {
    position: absolute; left: 424px; top: 150px;
    color: var(--brand-brown);
  }
  .contact__name { font-size: 17px; font-weight: 700; }
  .contact__role { font-size: 11px; margin-top: 3px; }
  .contact__list { list-style: none; margin-top: 26px; }
  .contact__list li {
    display: flex; align-items: center; gap: 6px;
    font-size: 11px; margin-bottom: 7px;
  }
  .contact__list svg { width: 13px; height: 13px; flex: none; }

  .social {
    position: absolute; left: 340px; top: 244px;
    display: flex; gap: 8px;
  }
  .social__dot {
    width: 18px; height: 18px; border-radius: 50%;
    background: var(--brand-brown);
  }
  .band {
    position: absolute; left: 0; right: 0; bottom: 0;
    height: 12px; background: var(--band-brown);
  }
</style>
</head>
<body>
<main class="canvas">

  <section class="card card--front" aria-label="Business card front">
    <div class="brand">
      <div class="wordmark">Bram Keystone Homes</div>
      <p class="slogan">- HOME RENOVATIONS - CUSTOM PROJECT DESIGN -</p>
    </div>
  </section>

  <section class="card card--back" aria-label="Business card back">
    <div class="brand">
      <div class="wordmark">Bram Keystone Homes</div>
      <p class="slogan">- HOME RENOVATIONS - CUSTOM PROJECT DESIGN -</p>
    </div>

    <div class="divider"></div>

    <div class="contact">
      <p class="contact__name">Ludovic Entrasse</p>
      <p class="contact__role">President / Ceo</p>
      <ul class="contact__list">
        <li>
          <svg viewBox="0 0 16 16" aria-hidden="true">
            <circle cx="8" cy="8" r="8" fill="#7a3f14"/>
            <path d="M5.2 4.2l1.4-.2.8 2-1 .8a5 5 0 0 0 2.8 2.8l.8-1 2 .8-.2 1.4c-3.6.4-7-3-6.6-6.6z" fill="#1d2022"/>
          </svg>
          519.604.3087
        </li>
        <li>
          <svg viewBox="0 0 16 16" aria-hidden="true">
            <circle cx="8" cy="8" r="8" fill="#7a3f14"/>
            <rect x="4" y="5" width="8" height="6" fill="none" stroke="#1d2022" stroke-width="1.2"/>
            <path d="M4 5l4 3.2L12 5" fill="none" stroke="#1d2022" stroke-width="1.2"/>
          </svg>
          info@keystonemail.com
        </li>
      </ul>
    </div>

    <div class="social" aria-label="Social media">
      <span class="social__dot"></span>
      <span class="social__dot"></span>
    </div>

    <div class="band"></div>
  </section>

</main>
</body>
</html>
```